Brivane Management

We need a web design for a new consulting company, with clients all over the world. The company provides management consulting to the travel industry.

Logo files are attached.

Website must look very corporate and be responsive in design.

Management Consulting

```html
<!DOCTYPE html>
<html lang="en">
<head>
<meta charset="utf-8">
<title>Brivane Management</title>
<link rel="stylesheet" href="https://fonts.googleapis.com/css2?family=Lato:wght@400;700&family=Oswald:wght@300;400&family=Lora:wght@400&family=Bitter:wght@400&display=swap">
<style>
:root{
  --navy:#1b1f4f;
  --green:#68ad28;
  --blue:#0c6fc8;
  --blue-dark:#0a5eae;
  --text:#3a3a3a;
  --muted:#555;
  --rule:#dcdcdc;
  --band:#ebebeb;
  --white:#fff;
}
*{margin:0;padding:0;box-sizing:border-box}
html,body{width:756px;height:1200px;overflow:hidden;background:var(--white)}
body{position:relative;font-family:'Lato',sans-serif;color:var(--text)}
.abs{position:absolute}

/* header */
.site-header{position:absolute;left:0;top:0;width:756px;height:65px;background:var(--white)}
.brand{position:absolute;left:83px;top:17px;display:flex;align-items:center;gap:8px}
.brand-mark{width:32px;height:32px;border-radius:50%;background:var(--green)}
.brand-name{font-family:'Lora',serif;font-size:17px;color:var(--navy);letter-spacing:.5px}
.main-nav{position:absolute;top:30px;right:84px;display:flex;font-size:8.5px;color:#222;letter-spacing:.4px}
.main-nav a{color:inherit;text-decoration:none;padding:0 20px;border-left:1px solid #ddd;line-height:11px}
.main-nav a:first-child{border-left:0}
.main-nav a:last-child{padding-right:0}

/* hero */
.hero{position:absolute;left:0;top:65px;width:756px;height:298px;
  background:radial-gradient(circle at 25% 60%,#eef1f2 0%,#cfd9dc 35%,#93adb3 70%,#7a989f 100%)}
.hero-title{position:absolute;right:84px;top:100px;text-align:right;font-family:'Oswald',sans-serif;font-weight:300;
  font-size:27px;line-height:35.5px;color:var(--white);text-transform:uppercase}

/* section heads */
.section-title{position:absolute;left:0;width:756px;text-align:center;font-family:'Lora',serif;font-size:19.5px;color:var(--navy);letter-spacing:1.2px}
.section-sub{position:absolute;left:0;width:756px;text-align:center;font-family:'Lato',sans-serif;font-size:9.5px;color:var(--green);letter-spacing:1px}
.section-rule{position:absolute;left:83px;width:590px;height:1px;background:var(--rule)}

.btn{position:absolute;background:var(--blue);color:var(--white);font-size:8.5px;text-align:center;line-height:20px;height:20px;letter-spacing:.3px}

/* welcome */
.welcome-lead{position:absolute;left:83px;top:454px;width:590px;text-align:center;font-size:7.8px;font-weight:700;color:#222}
.welcome-body{position:absolute;left:95px;top:474px;width:566px;text-align:center;font-size:7.8px;line-height:12.3px;color:var(--muted)}

/* services */
.services{position:absolute;left:0;top:582px;width:756px;height:213px;background:var(--band)}
.service-card{position:absolute;top:18px;width:139px;height:177px;background:var(--white)}
.service-photo{position:absolute;left:3px;top:3px;width:133px;height:76px}
.service-title{position:absolute;left:0;top:88px;width:139px;text-align:center;font-family:'Bitter',serif;font-size:11.5px;color:#222;letter-spacing:.3px}
.service-text{position:absolute;left:8px;top:110px;width:123px;text-align:center;font-size:7.8px;line-height:14px;color:var(--muted)}
.service-card .btn{left:36px;top:146px;width:66px}

/* testimonials */
.testimonial{position:absolute;top:894px;width:268px;height:75px;border:1px solid #d6d6d6;border-radius:3px;background:var(--white)}
.testimonial-tail{position:absolute;left:24px;bottom:-12px;width:20px;height:12px}
.avatar{position:absolute;left:9px;top:10px;width:56px;height:56px;border-radius:50%;border:2px solid #e2e2e2;background:var(--white)}
.avatar span{position:absolute;inset:3px;border-radius:50%}
.quote{position:absolute;left:74px;top:12px;width:186px;font-size:7.8px;line-height:12.3px;color:#333;text-indent:14px}
.quote::before{content:"\201C";position:absolute;left:-14px;top:-4px;font-family:'Lora',serif;font-size:18px;color:#bbb}
.client-name{position:absolute;top:990px;font-size:7.8px;font-weight:700;color:var(--navy)}

/* footer */
.site-footer{position:absolute;left:0;top:1028px;width:756px;height:145px;background:var(--blue)}
.footer-col{position:absolute;top:14px}
.footer-heading{font-family:'Bitter',serif;font-size:11px;color:var(--white);padding-bottom:8px;border-bottom:1px solid rgba(255,255,255,.25)}
.footer-list{list-style:none;font-size:8px;color:var(--white)}
.footer-list li{position:absolute;white-space:nowrap}
.footer-icon{position:absolute;left:0}
.newsletter-text{position:absolute;top:44px;width:140px;font-size:7.8px;line-height:11px;color:var(--white)}
.email-field{position:absolute;top:75px;left:0;width:127px;height:20px;background:var(--white);font-size:7px;color:#777;line-height:20px;padding-left:6px}
.subscribe{position:absolute;top:104px;left:0;width:61px;height:20px;background:var(--blue-dark);color:var(--white);font-size:8px;line-height:20px;text-align:center}
.social-dot{position:absolute;left:0;width:15px;height:15px;border-radius:50%;background:var(--white)}
.legal{position:absolute;left:0;top:1173px;width:756px;height:27px;background:var(--blue-dark);color:var(--white);font-size:8px;text-align:center;line-height:27px}
</style>
</head>
<body>

<header class="site-header">
  <div class="brand">
    <span class="brand-mark"></span>
    <span class="brand-name">BRIVANE MANAGEMENT</span>
  </div>
  <nav class="main-nav">
    <a href="#">HOME</a><a href="#">ABOUT US</a><a href="#">SERVICES</a><a href="#">CONTACT US</a>
  </nav>
</header>

<section class="hero" role="img" aria-label="Photo of a row of white spheres on a curved white arrow led by one red sphere, on a grey-teal background">
  <h1 class="hero-title">We provides<br>management consulting<br>to the travel industry.</h1>
</section>

<section class="welcome">
  <h2 class="section-title" style="top:391px">WELCOME BRIVANE</h2>
  <p class="section-sub" style="top:417px">STRATEGY MANAGEMENT, INC.</p>
  <div class="section-rule" style="top:440px"></div>
  <p class="welcome-lead">Lorem ipsum dolor sit amet, consectetur adipisicing elit, sed do eiusmod tem incididunt ut labore et dolore magna aliqua. Ut enim ad minim veniam.</p>
  <p class="welcome-body">Duis aute irure dolor in reprehenderitnin voliuptate velit esse cillum dolore eu fugiat nulla pariatur Excepteur sint occaecat cupidatat non proident, sunt in culpa qui officia deserunt mollit anim id est laborum Neque porro quisquam est, qui dolorem ipsum qus consectetur adipisci velit, sed quia non numquam eius modi tempora incidunt ut labore et dol magnam aliquam quaerat voluptatem. Ut enim ad minima veniam, quis nostrum exer ullam corporis suscipit laboriosam nisi ut aliquid ex ea commodi consequatur.</p>
  <a class="btn" style="left:346px;top:533px;width:65px">READ MORE</a>
</section>

<section class="services">
  <article class="service-card" style="left:83px">
    <div class="service-photo" role="img" aria-label="Photo of business people shaking hands in an office" style="background:linear-gradient(135deg,#dfe6ee,#3b4b66 60%,#1d2838)"></div>
    <h3 class="service-title">Account Management</h3>
    <p class="service-text">Duis aute irure dolor in rderi voliuptate velit esse.</p>
    <a class="btn">READ MORE</a>
  </article>
  <article class="service-card" style="left:233px">
    <div class="service-photo" role="img" aria-label="Photo of business travellers standing in a line with luggage" style="background:linear-gradient(180deg,#eef0f2,#9aa0a8 55%,#2b2f36)"></div>
    <h3 class="service-title">Traveller Tools</h3>
    <p class="service-text">Duis aute irure dolor in rderi voliuptate velit esse.</p>
    <a class="btn">READ MORE</a>
  </article>
  <article class="service-card" style="left:384px">
    <div class="service-photo" role="img" aria-label="Photo of a calculator, pen and financial chart" style="background:linear-gradient(135deg,#5d7fb8,#a9c0e4 55%,#e6eef8)"></div>
    <h3 class="service-title">Expense Management</h3>
    <p class="service-text">Duis aute irure dolor in rderi voliuptate velit esse.</p>
    <a class="btn">READ MORE</a>
  </article>
  <article class="service-card" style="left:535px">
    <div class="service-photo" role="img" aria-label="Photo of a traveller pulling a suitcase through an airport terminal" style="background:linear-gradient(180deg,#c6d3de,#8fa3b6 60%,#56697b)"></div>
    <h3 class="service-title">Travel Programs</h3>
    <p class="service-text">Duis aute irure dolor in rderi voliuptate velit esse.</p>
    <a class="btn">READ MORE</a>
  </article>
</section>

<section class="testimonials">
  <h2 class="section-title" style="top:823px">CLIENT TESTIMONIALS</h2>
  <p class="section-sub" style="top:849px">NEQUE PORRO QUISQUA MOLOREM</p>
  <div class="section-rule" style="top:872px"></div>

  <blockquote class="testimonial" style="left:100px">
    <div class="avatar"><span role="img" aria-label="Client portrait photo" style="background:linear-gradient(180deg,#e9d2b8,#c89a70)"></span></div>
    <p class="quote">Lorem ipsu donlor amet, consecte admsicn elt sed do eiusmod tempor incididunt utboret dolorie magna aliqua. Ut enim ad minienia quis nosinttrud exercitation ullamco laboriisi.</p>
    <svg class="testimonial-tail" viewBox="0 0 20 12"><path d="M0 0 L4 12 L20 0" fill="#fff" stroke="#d6d6d6"/><path d="M1 0 H19" stroke="#fff" stroke-width="2"/></svg>
  </blockquote>
  <p class="client-name" style="left:100px">Miss. Client Name</p>

  <blockquote class="testimonial" style="left:387px">
    <div class="avatar"><span role="img" aria-label="Client portrait photo" style="background:linear-gradient(180deg,#d9c1a6,#4a5363)"></span></div>
    <p class="quote">Lorem ipsu donlor amet, consecte admsicn elt sed do eiusmod tempor incididunt utboret dolorie magna aliqua. Ut enim ad minienia quis nosinttrud exercitation ullamco laboriisi.</p>
    <svg class="testimonial-tail" viewBox="0 0 20 12"><path d="M0 0 L4 12 L20 0" fill="#fff" stroke="#d6d6d6"/><path d="M1 0 H19" stroke="#fff" stroke-width="2"/></svg>
  </blockquote>
  <p class="client-name" style="left:387px">Mr. Client Name</p>
</section>

<footer class="site-footer">
  <div class="footer-col" style="left:83px;width:98px">
    <h4 class="footer-heading">Quick Links</h4>
    <ul class="footer-list">
      <li style="top:45px;left:0"><svg width="7" height="7" viewBox="0 0 7 7" style="margin-right:7px"><path d="M0 3.5H6M3.5 1L6 3.5L3.5 6" stroke="#fff" fill="none" stroke-width="1.1"/></svg>Home</li>
      <li style="top:67px;left:0"><svg width="7" height="7" viewBox="0 0 7 7" style="margin-right:7px"><path d="M0 3.5H6M3.5 1L6 3.5L3.5 6" stroke="#fff" fill="none" stroke-width="1.1"/></svg>About Us</li>
      <li style="top:88px;left:0"><svg width="7" height="7" viewBox="0 0 7 7" style="margin-right:7px"><path d="M0 3.5H6M3.5 1L6 3.5L3.5 6" stroke="#fff" fill="none" stroke-width="1.1"/></svg>Services</li>
      <li style="top:109px;left:0"><svg width="7" height="7" viewBox="0 0 7 7" style="margin-right:7px"><path d="M0 3.5H6M3.5 1L6 3.5L3.5 6" stroke="#fff" fill="none" stroke-width="1.1"/></svg>Contact Us</li>
    </ul>
  </div>

  <div class="footer-col" style="left:208px;width:156px">
    <h4 class="footer-heading">Contact Information</h4>
    <ul class="footer-list">
      <li style="top:41px;left:0;line-height:11.5px">
        <svg class="footer-icon" width="8" height="11" viewBox="0 0 8 11" style="top:2px"><path d="M4 0C1.8 0 0 1.7 0 3.9 0 6.8 4 11 4 11S8 6.8 8 3.9C8 1.7 6.2 0 4 0Z" fill="#fff"/><circle cx="4" cy="4" r="1.5" fill="#0c6fc8"/></svg>
        <div style="margin-left:19px"><b>BRIVANE</b><br>00 Neque porro quisquam&nbsp; dolor<br>qus consectetur. 000 000</div>
      </li>
      <li style="top:89px;left:0">
        <svg class="footer-icon" width="8" height="10" viewBox="0 0 8 10" style="top:1px"><path d="M1.5 0L3.2 2.6 2.2 3.6C2.7 5 3.6 6.2 4.8 7L5.8 6 8 7.8 6.8 9.5C3.2 9 0.4 5.2 0 1.3Z" fill="#fff"/></svg>
        <span style="margin-left:19px">(123) 456 7890</span>
      </li>
      <li style="top:110px;left:0">
        <svg class="footer-icon" width="9" height="7" viewBox="0 0 9 7" style="top:2px"><rect width="9" height="7" fill="#fff"/><path d="M0 0L4.5 3.8 9 0" stroke="#0c6fc8" fill="none"/></svg>
        <span style="margin-left:19px">info@yoursitename.com</span>
      </li>
    </ul>
  </div>

  <div class="footer-col" style="left:393px;width:127px">
    <h4 class="footer-heading">Newsletter Sign Up</h4>
    <p class="newsletter-text">Lorem ipsudolor sit coec adipiscing elitsite amet</p>
    <div class="email-field">Your Email</div>
    <div class="subscribe">SUBSCRIBE</div>
  </div>

  <div class="footer-col" style="left:562px;width:111px">
    <h4 class="footer-heading">Follow Us</h4>
    <ul class="footer-list">
      <li style="top:47px;left:0"><span class="social-dot" style="top:-3px"></span><span style="margin-left:27px">Linkface</span></li>
      <li style="top:70px;left:0"><span class="social-dot" style="top:-3px"></span><span style="margin-left:27px">Chirper</span></li>
      <li style="top:93px;left:0"><span class="social-dot" style="top:-3px"></span><span style="margin-left:27px">Orbit+</span></li>
    </ul>
  </div>
</footer>

<p class="legal">© 2014 Brivane. All Right reserved.</p>

</body>
</html>
```